Business Card for Coastal Tundrabridge Advisory

We need a business card for Coastal Tundrabridge Advisory. The company website address is provided below. The company logo is attached. We provide specialized permafrost services to the mining, transportation, and oil & gas industries. The card should be prepared for:
Matthias Korhonen, PhD.
Coastal Tundrabridge Advisory
PO Box 418259
Quillwater, Alaska 99642
Direct: +1-907-555-0143
Email: mkorhonen@tundrabridgeadvisory.example
Website: www.coastaltundrabridgeadvisory.example

```html
<!DOCTYPE html>
<html lang="en">
<head>
<meta charset="utf-8">
<title>Coastal Tundrabridge Advisory – Business Card</title>
<link rel="stylesheet" href="https://fonts.googleapis.com/css2?family=Montserrat:wght@400;600;700&display=swap">
<style>
  :root {
    --page-bg: #ecebe8;
    --card-bg: #ffffff;
    --ink: #1a1d24;
    --ink-soft: #2a2a2c;
    --band-dark: #2f2e30;
    --band-grey: #6b6b6b;
    --on-dark: #ffffff;
  }
  * { margin: 0; padding: 0; box-sizing: border-box; }
  html, body {
    width: 900px; height: 1200px; overflow: hidden;
    background: var(--page-bg);
    font-family: "Montserrat", Arial, sans-serif;
    color: var(--ink);
  }
  .canvas { position: relative; width: 900px; height: 1200px; }
  .card {
    position: absolute; left: 80px; width: 742px; height: 442px;
    background: var(--card-bg); border-radius: 40px; overflow: hidden;
  }
  .card--front { top: 130px; }
  .card--back { top: 638px; }

  .wordmark {
    position: absolute; font-weight: 700; text-transform: uppercase;
    color: var(--ink); line-height: 1.05; letter-spacing: 3px;
  }
  .card--front .wordmark { left: 55px; top: 52px; font-size: 31px; }
  .card--back .wordmark {
    left: 0; right: 0; top: 168px; text-align: center; font-size: 40px;
  }

  .holder { position: absolute; left: 28px; top: 183px; }
  .holder__name { font-size: 25px; font-weight: 700; color: var(--ink); }
  .holder__title { font-size: 15px; font-weight: 400; margin-top: 3px; padding-left: 2px; color: var(--ink-soft); }

  .contact-band { position: absolute; left: 0; top: 257px; width: 742px; height: 103px; }
  .contact-list {
    position: absolute; left: 45px; top: 277px; list-style: none;
    color: var(--on-dark); font-size: 15.5px; line-height: 22px;
  }
  .contact-list li { display: flex; align-items: center; gap: 10px; }
  .contact-list svg { width: 15px; height: 13px; fill: var(--on-dark); flex: none; }

  .address {
    position: absolute; left: 42px; top: 377px;
    font-size: 15.5px; line-height: 20px; color: var(--ink-soft);
  }
</style>
</head>
<body>
<div class="canvas">
  <section class="card card--front">
    <div class="wordmark">Coastal Tundrabridge<br>Advisory</div>

    <div class="holder">
      <div class="holder__name">Matthias Korhonen, PhD.</div>
      <div class="holder__title">CEO &amp; Founder</div>
    </div>

    <svg class="contact-band" viewBox="0 0 742 103" aria-hidden="true">
      <polygon points="0,0 508,0 460,103 0,103" fill="var(--band-dark)"/>
      <polygon points="520,0 742,0 742,103 468,103" fill="var(--band-grey)"/>
    </svg>

    <ul class="contact-list">
      <li>
        <svg viewBox="0 0 16 14"><path d="M1 5c0-2 2-4 7-4s7 2 7 4v1h-4V4H5v2H1zM3 7h10l1 6H2z"/></svg>
        +1-907-555-0143
      </li>
      <li>
        <svg viewBox="0 0 16 14"><path d="M1 2h14v1L8 8 1 3zM1 5l7 5 7-5v8H1z"/></svg>
        mkorhonen@tundrabridgeadvisory.example
      </li>
      <li>
        <svg viewBox="0 0 16 14"><circle cx="8" cy="7" r="6.5"/><path d="M5 4l3 1 1 3-2 2-1-2-2-1z" fill="var(--band-dark)"/></svg>
        www.coastaltundrabridgeadvisory.example
      </li>
    </ul>

    <div class="address">PO Box 418259<br>Quillwater, Alaska 99642</div>
  </section>

  <section class="card card--back">
    <div class="wordmark">Coastal Tundrabridge<br>Advisory</div>
  </section>
</div>
</body>
</html>
```